Brightwave Reach - Business Card

We need a business card for a Social Media Marketing company that specializes in online marketing for small businesses in Canada using common Social Media platforms such as Pixlora, Chatterly, Blinkpost & Quibber.

I have uploaded a copy of our logo which I would like utilized in the business card. We would like the business card to be modern yet classy design.

Our website is www.brightwavereach.ca

Industry/Entity Type

Marketing

Contact Information for Business Card

Email: info@brightwavereach.ca
Website: www.brightwavereach.ca
Telephone: 604-555-0193

Colors

Designer to choose colors to be used in the design.

Requirements
Must have
• Social Media icons on reverse
• Please add some designs with color.

```html
<!DOCTYPE html>
<html lang="en">
<head>
<meta charset="utf-8">
<title>Brightwave Reach – Business Card</title>
<link rel="stylesheet" href="https://fonts.googleapis.com/css2?family=Roboto:wght@400;500&family=Roboto+Condensed:wght@700&display=swap">
<style>
  :root {
    --backdrop: #e4e4e4;
    --card-light: #f5f5f4;
    --card-dark: #3a3e41;
    --ink: #3b3e41;
    --ink-soft: #4f5256;
    --ink-muted: #a9abad;
    --on-dark: #f2f2f2;
    --rule-on-dark: #8d9093;
  }
  * { box-sizing: border-box; margin: 0; padding: 0; }
  html, body {
    width: 1200px; height: 960px; overflow: hidden;
    background: var(--backdrop);
    font-family: "Roboto", Arial, sans-serif;
  }
  .canvas { position: relative; width: 1200px; height: 960px; }

  .card { position: absolute; width: 600px; height: 343px; overflow: hidden; }
  .card--front { left: 314px; top: 113px; background: var(--card-light); }
  .card--back  { left: 311px; top: 472px; background: var(--card-dark); }

  .backdrop-mark {
    position: absolute; left: 290px; top: 20px; width: 320px; height: 330px;
    background: radial-gradient(ellipse at 55% 50%, rgba(190,190,190,.55) 0%, rgba(205,205,205,.3) 45%, rgba(245,245,244,0) 72%);
  }

  .brand {
    font-family: "Roboto Condensed", "Arial Narrow", sans-serif;
    font-weight: 700; text-transform: uppercase; text-align: center;
    line-height: 1.02; letter-spacing: .5px;
  }
  .brand--front {
    position: absolute; left: 48px; top: 76px; width: 178px;
    font-size: 31px; color: var(--ink);
  }
  .brand--back {
    position: absolute; left: 0; top: 118px; width: 600px;
    font-size: 37px; color: var(--on-dark);
  }

  .contact {
    position: absolute; left: 50px; top: 241px; list-style: none;
    font-size: 14px; color: var(--ink-soft);
  }
  .contact li { display: flex; align-items: center; height: 19px; }
  .contact svg { width: 12px; height: 12px; margin-right: 10px; fill: var(--ink); }

  .person { position: absolute; right: 50px; top: 246px; text-align: right; }
  .person__name {
    font-family: "Roboto Condensed", "Arial Narrow", sans-serif;
    font-weight: 700; font-size: 19px; color: var(--ink-soft);
  }
  .person__role { font-size: 14px; color: var(--ink-muted); margin-top: 3px; }
  .edge-tab {
    position: absolute; right: 0; top: 250px; width: 12px; height: 37px;
    background: var(--card-dark);
  }

  .social {
    position: absolute; left: 0; top: 286px; width: 600px;
    display: flex; align-items: center; justify-content: center; gap: 12px;
  }
  .social__rule { width: 125px; height: 1px; }
  .social__rule--left  { background: linear-gradient(to right, rgba(141,144,147,0), var(--rule-on-dark)); }
  .social__rule--right { background: linear-gradient(to left, rgba(141,144,147,0), var(--rule-on-dark)); }
  .social__list { display: flex; gap: 10px; list-style: none; }
  .social__item {
    display: flex; align-items: center; gap: 4px;
    font-size: 11px; color: var(--on-dark);
  }
  .social__dot {
    width: 8px; height: 8px; border-radius: 50%; border: 1px solid var(--on-dark);
  }
</style>
</head>
<body>
<main class="canvas">
  <section class="card card--front" aria-label="Card front">
    <div class="backdrop-mark" role="img" aria-label="Faint textured backdrop shape"></div>
    <div class="brand brand--front">Brightwave<br>Reach</div>
    <ul class="contact">
      <li><svg viewBox="0 0 24 24" aria-hidden="true"><path d="M6.6 10.8a15.1 15.1 0 0 0 6.6 6.6l2.2-2.2c.3-.3.7-.4 1-.2 1.1.4 2.3.6 3.6.6.6 0 1 .4 1 1V20c0 .6-.4 1-1 1A17 17 0 0 1 3 4c0-.6.4-1 1-1h3.5c.6 0 1 .4 1 1 0 1.3.2 2.5.6 3.6.1.3 0 .7-.2 1z"/></svg>604-555-0193</li>
      <li><svg viewBox="0 0 24 24" aria-hidden="true"><path d="M2 5h20v14H2zm2 2v.5l8 5 8-5V7l-8 5z"/></svg>info@brightwavereach.ca</li>
      <li><svg viewBox="0 0 24 24" aria-hidden="true"><circle cx="12" cy="12" r="10"/></svg>www.brightwavereach.ca</li>
    </ul>
    <div class="person">
      <div class="person__name">DANIEL MARSH</div>
      <div class="person__role">CEO/FOUNDER</div>
    </div>
    <div class="edge-tab"></div>
  </section>

  <section class="card card--back" aria-label="Card back">
    <div class="brand brand--back">Brightwave<br>Reach</div>
    <div class="social">
      <span class="social__rule social__rule--left"></span>
      <ul class="social__list">
        <li class="social__item"><span class="social__dot"></span>Chatterly</li>
        <li class="social__item"><span class="social__dot"></span>Pixlora</li>
        <li class="social__item"><span class="social__dot"></span>Quibber</li>
      </ul>
      <span class="social__rule social__rule--right"></span>
    </div>
  </section>
</main>
</body>
</html>
```